New Business card design to reflect rebrand

I would like a business card design with a good base colour for our new logo and also a placeholder for a profile pic of the card holder. the design needs to be editable to the point that we can easily change the picture of the person and use that design for printmerlo etc. we are looking at a metalic finish business card so will need a good base colour to bring out the finish.

Target Market(s)

prospective customers

Industry/Entity Type

Business

Contact Information for Business Card

I would like one editable design that we can change the name of the card holder and profile picture. The design need to be in a format that be send to printmerlo etc.

Our address is Fenwick Lodge, Copse Lane, Ashcombe Vale, GU14 3TP Tel no. 01483 556172

Requirements
Must have
• place holder for a profile pic for the card holder. in AI or preferably PSD format

```html
<!DOCTYPE html>
<html lang="en">
<head>
<meta charset="utf-8">
<title>Brightfold Workplace Services – Business Card</title>
<link rel="stylesheet" href="https://fonts.googleapis.com/css2?family=Open+Sans:wght@400;600;700&display=swap">
<style>
  :root {
    --backdrop: #e9e6e2;
    --card-black: #141414;
    --slate: #5a6f8a;
    --orange: #f26a1b;
    --ink-white: #f2f2f2;
    --silver: #b9b9b9;
    --photo-top: #6f86a3;
    --photo-bottom: #2b3443;
  }
  * { box-sizing: border-box; margin: 0; padding: 0; }
  html, body {
    width: 1200px; height: 900px; overflow: hidden;
    background: var(--backdrop);
    font-family: "Open Sans", Arial, sans-serif;
  }
  .canvas {
    position: relative; width: 1200px; height: 900px;
    display: flex; align-items: center; justify-content: center; gap: 50px;
  }
  .card {
    position: relative; width: 525px; height: 300px;
    background: var(--card-black);
    border-radius: 4px;
    box-shadow: 0 10px 30px rgba(0,0,0,.25);
    overflow: hidden;
  }
  /* Front */
  .profile-photo {
    position: absolute; left: 42px; top: 40px;
    width: 170px; height: 180px; border-radius: 50%;
    background: radial-gradient(circle at 50% 35%, var(--photo-top), var(--photo-bottom));
  }
  .holder-name {
    position: absolute; left: 48px; top: 234px;
    font-size: 27px; font-weight: 600; letter-spacing: .2px; white-space: nowrap;
  }
  .holder-name .first { color: var(--slate); }
  .holder-name .last { color: var(--orange); }
  .brand-front {
    position: absolute; left: 252px; top: 62px;
    color: var(--slate); font-weight: 700; line-height: 1.05; white-space: nowrap;
  }
  .brand-front .brand-name { font-size: 34px; letter-spacing: 1px; }
  .brand-front .brand-sub { font-size: 14px; letter-spacing: 3.2px; }
  .contact {
    position: absolute; left: 252px; top: 142px;
    color: var(--ink-white); font-size: 13.5px; line-height: 1.45;
    list-style: none; white-space: nowrap;
  }
  .contact li { display: flex; align-items: center; gap: 7px; }
  .contact svg { width: 11px; height: 11px; fill: var(--orange); flex: none; }
  .contact .address { margin-top: 12px; display: block; }
  /* Back */
  .brand-back {
    position: absolute; inset: 0;
    display: flex; flex-direction: column; align-items: center; justify-content: center;
    color: var(--silver); font-weight: 700; line-height: 1.1; white-space: nowrap;
  }
  .brand-back .brand-name { font-size: 44px; letter-spacing: 2px; }
  .brand-back .brand-sub { font-size: 16px; letter-spacing: 4.5px; }
</style>
</head>
<body>
<main class="canvas">
  <section class="card card-front" aria-label="Card front">
    <div class="profile-photo" role="img" aria-label="Profile photo of the card holder"></div>
    <p class="holder-name"><span class="first">Daniel</span> <span class="last">Hart</span></p>
    <div class="brand-front">
      <div class="brand-name">BRIGHTFOLD</div>
      <div class="brand-sub">WORKPLACE SERVICES</div>
    </div>
    <ul class="contact">
      <li>
        <svg viewBox="0 0 24 24" aria-hidden="true"><path d="M6.6 10.8a15.2 15.2 0 0 0 6.6 6.6l2.2-2.2a1 1 0 0 1 1-.25 11.4 11.4 0 0 0 3.6.57 1 1 0 0 1 1 1V20a1 1 0 0 1-1 1A17 17 0 0 1 3 4a1 1 0 0 1 1-1h3.5a1 1 0 0 1 1 1c0 1.25.2 2.45.57 3.57a1 1 0 0 1-.25 1z"/></svg>
        01483 556172
      </li>
      <li>
        <svg viewBox="0 0 24 24" aria-hidden="true"><path d="M2 5h20v14H2z M2 5l10 8 10-8" /></svg>
        info@brightfold.co.uk
      </li>
      <li class="address">Fenwick Lodge, Copse Lane,<br>Ashcombe Vale, GU14 3TP</li>
    </ul>
  </section>

  <section class="card card-back" aria-label="Card back">
    <div class="brand-back">
      <div class="brand-name">BRIGHTFOLD</div>
      <div class="brand-sub">WORKPLACE SERVICES</div>
    </div>
  </section>
</main>
</body>
</html>
```